HARBORLINE AUTO GLASS

Mobile Glass Shop:

1) Windshield REPAIR 2)Windshield replacment 3) Rear Windshield Replacment 4) Side Window Replacment 5) car window replacment 6) Power Window Repair.

Schedual a service within 24 hour with one of our certified technicians.
Updates

See "brightvane auto repair" web site for referance on the nature of our buisness and service. www.brightvane-example.com

Coding

```html
<!DOCTYPE html>
<html lang="en">
<head>
<meta charset="utf-8">
<title>Harborline Auto Glass – Gallery</title>
<link rel="stylesheet" href="https://fonts.googleapis.com/css2?family=Bebas+Neue&family=Poppins:ital,wght@0,400;0,500;0,600;1,400&display=swap">
<style>
:root{
  --blue:#1f86c7;
  --blue-dark:#1569a3;
  --ink:#222;
  --dark:#232427;
  --red:#e8363a;
  --white:#fff;
}
*{box-sizing:border-box;margin:0;padding:0}
html,body{width:680px;height:1200px;overflow:hidden;background:var(--white)}
body{position:relative;font-family:"Poppins",sans-serif;color:var(--ink)}
.abs{position:absolute}

/* header */
.brand{display:flex;align-items:center;gap:6px;color:var(--blue);font-family:"Bebas Neue",sans-serif;line-height:.9}
.brand-mark{background:var(--blue);border-radius:3px}
.brand-name small{display:block;color:var(--blue)}
.header-brand{left:40px;top:18px}
.header-brand .brand-mark{width:28px;height:40px}
.header-brand .brand-name{font-size:20px}
.header-brand .brand-name small{font-size:11px;letter-spacing:3px}
.nav{left:224px;top:35px;font-size:8px;color:#333}
.nav a{position:absolute;white-space:nowrap;text-decoration:none;color:inherit}
.nav a.active{color:var(--blue);font-weight:500}
.nav a.active::after{content:"• • • • • •";position:absolute;left:3px;top:11px;font-size:3px;letter-spacing:1px;color:var(--blue)}
.call{left:518px;top:20px;display:flex;gap:8px;align-items:center}
.call-label{font-family:"Bebas Neue",sans-serif;font-size:10px;color:#222;line-height:1}
.call-number{font-family:"Bebas Neue",sans-serif;font-size:16px;color:var(--blue);line-height:1}

/* hero */
.hero{left:0;top:74px;width:680px;height:234px;background:linear-gradient(120deg,#4f8fae 0%,#3c6c86 40%,#5b7c95 70%,#2f4f70 100%)}
.hero-title{left:0;top:184px;width:680px;text-align:center;font-family:"Bebas Neue",sans-serif;font-size:21px;letter-spacing:1.5px;color:var(--white)}
.hero-wave{left:0;top:255px}

/* gallery */
.section-title{left:0;top:352px;width:680px;text-align:center;font-family:"Bebas Neue",sans-serif;font-weight:400;font-size:22px;letter-spacing:1.5px;color:#222}
.photo{border-radius:9px;overflow:hidden}
.overlay{background:rgba(45,125,160,.75)}
.overlay-plus{left:80px;top:105px}
.overlay-caption{left:0;top:182px;width:100%;text-align:center;color:var(--white);font-weight:600;font-size:14px}
.btn{display:flex;align-items:center;justify-content:center;gap:8px;color:var(--white);background:linear-gradient(90deg,var(--blue-dark),var(--blue));border-radius:14px;font-size:8px}

/* footer */
.footer-wave{left:0;top:898px}
.footer{left:0;top:940px;width:680px;height:214px;background:var(--dark)}
.footer-brand{left:36px;top:975px}
.footer-brand .brand-mark{width:44px;height:60px}
.footer-brand .brand-name{font-size:30px}
.footer-brand .brand-name small{font-size:12px;letter-spacing:6px}
.ficon{width:26px;height:26px;border-radius:50%;background:var(--blue);display:flex;align-items:center;justify-content:center}
.f-phone{left:70px;top:1050px;font-family:"Bebas Neue",sans-serif;font-size:20px;color:var(--red);line-height:1}
.f-email{left:71px;top:1070px;font-size:7.5px;color:var(--blue)}
.f-addr{left:72px;top:1089px;font-size:7.5px;color:var(--white);line-height:1.2}
.f-head{font-size:10.5px;letter-spacing:1px;color:var(--white);font-weight:500}
.f-dash{color:#ccc;font-size:9px;letter-spacing:2px}
.f-list{list-style:none;font-size:7.5px;color:var(--white)}
.f-list li{height:15.4px;white-space:nowrap}
.f-list li::before{content:"-";margin-right:6px}
.field{border:1px solid #555;font-size:7px;font-style:italic;color:#aaa;padding:3px 4px}
.f-submit{left:466px;top:1089px;width:82px;height:22px}

/* bottom bar */
.copy{left:42px;top:1169px;font-size:8px;color:#333}
.social{width:22px;height:22px;border-radius:50%;background:#222}
.social.first{background:var(--blue)}
</style>
</head>
<body>

<header>
  <div class="brand header-brand abs"><span class="brand-mark"></span><span class="brand-name">HARBORLINE<small>AUTO GLASS</small></span></div>
  <nav class="nav abs">
    <a style="left:0">Home</a>
    <a style="left:41px">About</a>
    <a style="left:84px">Services</a>
    <a style="left:135px">Insurance</a>
    <a class="active" style="left:193px">Gallery</a>
    <a style="left:241px">Contact</a>
  </nav>
  <div class="call abs">
    <svg width="26" height="26" viewBox="0 0 26 26" fill="none" stroke="#1f86c7" stroke-width="1.6"><path d="M6 3l4 4-2 3c1 3 4 6 7 7l3-2 4 4-3 3C11 22 4 15 3 6z"/><rect x="15" y="3" width="8" height="8" rx="2"/></svg>
    <div><div class="call-label">CALL US NOW</div><div class="call-number">000 555 010 246</div></div>
  </div>
</header>

<div class="hero abs" role="img" aria-label="Technicians fitting a new windshield with suction cups in a workshop"></div>
<svg class="hero-wave abs" width="680" height="60" viewBox="0 0 680 60">
  <path d="M0 8 C40 20 80 30 100 34 L0 44Z" fill="#1f86c7"/>
  <path d="M680 8 C640 20 600 30 580 34 L680 44Z" fill="#1f86c7"/>
  <path d="M0 44 C60 28 130 30 250 40 C300 45 320 45 330 41 C338 36 342 36 350 41 C360 45 380 45 430 40 C550 30 620 28 680 48 L680 60 L0 60Z" fill="#fff"/>
  <path d="M336 48l4 3 4-3M336 52l4 3 4-3" stroke="#222" stroke-width="1.3" fill="none"/>
</svg>
<div class="hero-title abs">GALLERY</div>

<h2 class="section-title abs">PHOTO GALLERY</h2>

<div class="photo abs" style="left:63px;top:391px;width:176px;height:103px;background:linear-gradient(135deg,#c9ccd0,#30394a 60%,#e6e7e9)" role="img" aria-label="Technician polishing a white car's tail light"></div>
<div class="photo abs" style="left:63px;top:507px;width:176px;height:102px;background:linear-gradient(135deg,#7a8088,#2d3138 55%,#2a63c0)" role="img" aria-label="Technician placing suction cups on a windshield"></div>
<div class="photo abs" style="left:252px;top:391px;width:176px;height:217px;background:linear-gradient(160deg,#3e4145,#6a6560 50%,#2c2e31)" role="img" aria-label="Technician testing wiring inside a car door"></div>
<div class="photo abs" style="left:440px;top:391px;width:176px;height:217px;background:linear-gradient(180deg,#2f5a3c,#5b6a5c 50%,#b36a33 70%,#6f7377)" role="img" aria-label="Orange sports car on a forest road">
  <div class="overlay abs" style="inset:0"></div>
  <svg class="overlay-plus abs" width="18" height="18" viewBox="0 0 18 18"><circle cx="9" cy="9" r="8" fill="none" stroke="#fff" stroke-width="1.4"/><path d="M9 5v8M5 9h8" stroke="#fff" stroke-width="1.4"/></svg>
  <div class="overlay-caption abs">Windshield Repair</div>
</div>

<div class="photo abs" style="left:62px;top:626px;width:177px;height:216px;background:linear-gradient(135deg,#222,#c99d86 35%,#6a8a7a 65%,#2a2d30)" role="img" aria-label="Close-up of a windshield chip being repaired"></div>
<div class="photo abs" style="left:251px;top:626px;width:176px;height:216px;background:linear-gradient(150deg,#8c8f92,#2a2c2e 45%,#c9a690 60%,#3a3d40)" role="img" aria-label="Windshield resin injector tool in use"></div>
<div class="photo abs" style="left:439px;top:626px;width:177px;height:102px;background:linear-gradient(135deg,#5d636b,#2c3340 50%,#2d58b8)" role="img" aria-label="Gloved hands lifting glass with suction cups"></div>
<div class="photo abs" style="left:439px;top:741px;width:177px;height:102px;background:linear-gradient(135deg,#d3d6da,#2a5fc0 45%,#1d1f22)" role="img" aria-label="Technician fitting windshield with blue suction cups"></div>

<div class="btn abs" style="left:295px;top:862px;width:93px;height:25px">VIEW MORE <span>&gt;&gt;</span></div>

<svg class="footer-wave abs" width="680" height="44" viewBox="0 0 680 44"><path d="M0 4 C200 50 480 50 680 0 L680 44 L0 44Z" fill="#232427"/></svg>
<footer class="footer abs"></footer>

<div class="brand footer-brand abs"><span class="brand-mark"></span><span class="brand-name">HARBORLINE<small>AUTO GLASS</small></span></div>

<div class="ficon abs" style="left:40px;top:1051px"><svg width="12" height="12" viewBox="0 0 24 24" fill="#fff"><path d="M5 2l5 5-2 3c1 3 4 6 7 7l3-2 5 5-3 3C10 23 1 14 2 5z"/></svg></div>
<div class="f-phone abs">000 555 010 246</div>
<div class="f-email abs">info@harborlineglass.example</div>
<div class="ficon abs" style="left:40px;top:1083px"><svg width="10" height="12" viewBox="0 0 20 24" fill="#fff"><path d="M10 0a8 8 0 018 8c0 6-8 16-8 16S2 14 2 8a8 8 0 018-8zm0 5a3 3 0 100 6 3 3 0 000-6z"/></svg></div>
<div class="f-addr abs">456 W. Marina Ave<br>#2210, Bayview, GA 12345</div>

<div class="f-dash abs" style="left:215px;top:1006px">- - - - -</div>
<ul class="f-list abs" style="left:214px;top:1024px">
  <li>Home</li><li>About</li><li>Services</li><li>Insurance</li><li>Gallery</li><li>Contact</li>
</ul>

<div class="f-head abs" style="left:307px;top:992px">SERVICES</div>
<div class="f-dash abs" style="left:307px;top:1006px">- - - - -</div>
<ul class="f-list abs" style="left:308px;top:1024px">
  <li>Windshield Repair</li><li>Windshield Replacment</li><li>Rear Windshield Replacment</li><li>Side Window Replacment</li><li>Car Window Teplacment</li><li>Power Window Repair</li>
</ul>

<div class="f-head abs" style="left:464px;top:992px">QUICK CONTACT</div>
<div class="f-dash abs" style="left:465px;top:1006px">- - - - -</div>
<div class="field abs" style="left:465px;top:1025px;width:54px;height:15px">Name*</div>
<div class="field abs" style="left:523px;top:1025px;width:55px;height:15px">Phone*</div>
<div class="field abs" style="left:582px;top:1025px;width:54px;height:15px">Email*</div>
<div class="field abs" style="left:465px;top:1045px;width:171px;height:38px">Message</div>
<div class="btn f-submit abs">SUBMIT</div>

<div class="copy abs">Copyright © HARBORLINE AUTO GLASS. All Rights Reserved.</div>
<div class="social first abs" style="left:533px;top:1165px"></div>
<div class="social abs" style="left:560px;top:1165px"></div>
<div class="social abs" style="left:587px;top:1165px"></div>
<div class="social abs" style="left:615px;top:1165px"></div>

</body>
</html>
```